Create a Brochure Design for Brantley Homecare

Brantley Homecare is a subsidiary of the Brantley Care Group. This brochure is specifically for the Brantley Homecare company and brand. Create a 3 panel, A4, front and back, tri-fold brochure. This brochure will be a way to introduce our Homecare services to the community, prospective clients, and various referral partners. The brochure must be eye catching, unique in its deliverables and demonstrate both attention to detail and comfort. Our organization is sophisticated and built around warmth, care and individualized personal attention. The most important aspect of this design is to focus on creating a nurturing, warm, and inviting feel where you would want to have a Nurse or Nurse’s Aide in your own home or a loved one’s home.

I am open to the creativity of the designer to develop something based on the above criteria; however I would like the design to work well with the existing collateral material. What I mean by that is that while I want everything to have its own personality and stand out as its own brand representative, I still need to be able to tell that the overall design concept stays stylistically inside of the same ‘family’ of existing designed material. Because of this, below I would like for the designer to pull inspiration from the link to our website (Located below) as well as from the attachment of our recently refreshed business cards (Attached). This should allow each design to be unique and creative, while still staying inside of a framework and the feel/style that I am looking for.

Finally, I want all the designers to understand that this brochure design is for a private, in home, healthcare company where we are responsible for providing personalized care for a culturally and ethnically diverse make-up clientele of all ages. The photos that are used must represent an image of warmth, care, and a positive interaction between client and caregiver.

Look under the Brantley Homecare tab at www.brantleycaregroup.example

Industry/Entity Type

Healthcare

Requirements
Must have
• • The Brantley Homecare company logo must be included.

```html
<!DOCTYPE html>
<html lang="en">
<head>
<meta charset="utf-8">
<title>Brantley Homecare – Services Brochure</title>
<link href="https://fonts.googleapis.com/css2?family=Crimson+Pro:wght@700&family=Source+Sans+3:ital,wght@0,400;0,600;1,400&display=swap" rel="stylesheet">
<style>
  :root{
    --teal:#1d6f6a;
    --peach:#f4a58c;
    --peach-light:#fbd9cc;
    --peach-soft:#fdeee8;
    --salmon:#ef8f78;
    --ink:#444444;
    --rule:#f0b7a4;
    --frame:#333333;
    --paper:#fffdfc;
  }
  *{margin:0;padding:0;box-sizing:border-box}
  html,body{width:1200px;height:900px;overflow:hidden;background:#ffffff}
  body{font-family:"Source Sans 3",Arial,sans-serif;color:var(--ink);font-size:12.6px;line-height:15px}
  .brochure{position:absolute;left:75px;top:79px;width:1050px;height:743px;border:1px solid var(--frame);background:var(--paper);overflow:hidden}
  .band{position:absolute;left:0;width:100%;height:14px;background:linear-gradient(90deg,var(--peach-light),var(--peach-soft) 35%,var(--peach-light) 65%,var(--peach))}
  .band--top{top:0}
  .band--bottom{bottom:0}
  .fold{position:absolute;top:0;bottom:0;width:1px;background:#9a9a9a}
  .panel{position:absolute;top:0;height:100%;width:350px}
  .panel--left{left:0}
  .panel--middle{left:350px}
  .panel--right{left:700px}
  .block{position:absolute}
  .title{font-family:"Crimson Pro",Georgia,serif;font-weight:700;color:var(--teal);font-size:23px;line-height:26px;position:absolute;left:0;width:350px;text-align:center;top:40px}
  .swash-area{position:absolute;left:140px;top:67px;width:70px;height:10px;border-radius:5px;background:linear-gradient(90deg,var(--peach-soft),var(--peach-light) 50%,var(--peach-soft))}
  .heading{color:var(--teal);font-size:15px;letter-spacing:.4px;line-height:18px;font-weight:400;text-transform:uppercase}
  .subhead{color:var(--peach);font-size:12.4px;line-height:14px}
  .rule{height:1px;background:var(--rule);margin-top:4px;width:292px}
  p{margin:0}
  .gap{margin-top:15px}
  .nowrap-tight{white-space:nowrap;letter-spacing:-.35px;font-size:12.2px}
  .list{list-style:none}
  .list--bullet li::before{content:"\2022\00a0";}
  .list--dots li{position:relative;padding-left:14px}
  .list--dots li::before{content:"";position:absolute;left:3px;top:6px;width:4px;height:4px;border-radius:50%;background:var(--teal)}
  .list--indent{padding-left:10px}
  .contact{font-size:12.4px}
  .contact em{font-style:italic}
  .photo{position:absolute;left:0;display:block}
</style>
</head>
<body>
<main class="brochure">
  <div class="band band--top"></div>
  <div class="band band--bottom"></div>
  <div class="fold" style="left:349px"></div>
  <div class="fold" style="left:699px"></div>

  <section class="panel panel--left">
    <h1 class="title">Services</h1>
    <div class="swash-area" role="img" aria-label="Decorative peach swash beneath the heading"></div>

    <svg class="photo" style="top:80px" width="350" height="200" viewBox="0 0 350 200">
      <defs>
        <linearGradient id="careGlow" x1="0" y1="0" x2="1" y2="1">
          <stop offset="0" stop-color="#e9ecf0"/>
          <stop offset=".55" stop-color="#e7cbbd"/>
          <stop offset="1" stop-color="#c89a86"/>
        </linearGradient>
      </defs>
      <path role="img" aria-label="Photo: a nurse listening to a young girl's back with a stethoscope while her mother smiles" d="M0 26 C120 30 250 20 350 22 L350 158 C250 158 130 175 0 200 Z" fill="url(#careGlow)"/>
      <path d="M0 30 C110 30 260 26 350 0 L350 14 C260 34 110 34 0 34 Z" fill="#f7c3b1"/>
      <path d="M0 38 C110 36 260 34 350 2" fill="none" stroke="#fbe2d9" stroke-width="3"/>
      <path d="M0 190 C70 176 180 150 350 158 L350 200 L0 200 Z" fill="var(--paper)"/>
      <path d="M0 186 C80 168 190 148 350 152 L350 160 C200 156 90 176 0 196 Z" fill="#f6b7a2"/>
    </svg>

    <div class="block" style="left:43px;top:288px;width:300px">
      <p>Brantley Homecare provides two different levels of care.<br><span class="nowrap-tight">Our Nurse Care Consultant will assist the client and family</span><br>in determining the appropriate level of care needed<br>during the complimentary initial consultation.</p>
      <ul class="list list--dots list--indent gap">
        <li>Nurse Aide Care</li>
        <li>Skilled Nursing Care</li>
      </ul>
      <p class="gap">Clients who already receive personal care services<br>can also have the following additional support<br>services.</p>
      <ul class="list list--dots gap">
        <li>Medication Services</li>
        <li>Transportation Services</li>
      </ul>
      <h2 class="heading" style="margin-top:14px">Your Schedule</h2>
      <p style="margin-top:13px">Brantley Homecare is flexible with your care needs.<br>As you need more or less care, your schedule can<br>be adjusted to accommodate your needs. We have<br>found that a set schedule works best (same days<br>and times each week). This allows you to be able to<br>depend on the same care professional(s) each week.<br>You determine the schedule, from a minimum of<br>four hours per shift to 24 hours of care per day,<br>7 days per week, 365 days per year.</p>
    </div>
  </section>

  <section class="panel panel--middle">
    <div class="block" style="left:29px;top:46px;width:300px">
      <h2 class="heading">Nurse Aide Care</h2>
      <p class="subhead">(4-hour minimum shift up to 24 hour care)</p>
      <div class="rule"></div>
      <p style="margin-top:10px">Our Nurse Aides help you with your personal care<br>needs, provide companionship, run errands, and do<br>light housekeeping, along with assisting you with<br>the activities of daily living.</p>
      <ul class="list list--bullet gap">
        <li>Companionship</li>
        <li>Meal Preparation</li>
        <li>Medication Reminders</li>
        <li>Light Housekeeping</li>
        <li>Personal Care</li>
      </ul>
      <h2 class="heading" style="margin-top:26px">Skilled Nursing Care</h2>
      <p class="subhead">(2-hour minimum shift up to 24 hour care)</p>
      <div class="rule"></div>
      <p style="margin-top:10px">We offer a wide range of skilled nursing services<br>using RN’s and LPN’s who provide treatment from<br>wound care to life support, in addition to all of the<br>services performed by our Nurse Aides.</p>
      <ul class="list list--bullet gap">
        <li>Wound Care</li>
        <li>Medication Administration</li>
        <li>Ventilator Care</li>
        <li>Pain Management</li>
        <li>Oxygen Therapy</li>
        <li>Catheter Insertion</li>
        <li>Patient Teaching</li>
        <li>Injections</li>
        <li>G-Tube Feeding</li>
        <li>IV Therapy</li>
      </ul>
      <p class="gap">Our Nurses can also provide personal care assistance,<br>light housekeeping, and meal preparation. In addition,<br>We offer a wide range of skilled nursing services using<br>RN’s and LPN’s who provide treatment from wound<br>care to life support</p>
    </div>
    <div class="rule" style="position:absolute;left:29px;top:650px"></div>
    <p class="block contact" style="left:29px;top:662px">For more information please check our website<br><em>http://www.brantleycaregroup.example/homecare/</em> ,<br>or call us at 808-555-0142.</p>
  </section>

  <section class="panel panel--right">
    <div class="block" style="left:15px;top:46px;width:300px">
      <h2 class="heading">Medication Services</h2>
      <div class="rule" style="margin-top:5px"></div>
      <p style="margin-top:10px">Brantley Homecare clients who already receive personal<br>care services may choose to have our Licensed Nurse<br>pre-pour their medications.</p>
      <p class="gap">Our Nurse will pre-pour your medication in weekly pill<br>containers for a 28-day period. A list of the medications<br>you take, including over-the-counter medications, will<br>be provided to your physician for written authorization.</p>
    </div>

    <svg class="photo" style="top:216px" width="350" height="200" viewBox="0 0 350 200">
      <defs>
        <linearGradient id="pharmacyGlow" x1="0" y1="0" x2="1" y2="0">
          <stop offset="0" stop-color="#cfc6c0"/>
          <stop offset=".45" stop-color="#eef0ee"/>
          <stop offset="1" stop-color="#d8d0c8"/>
        </linearGradient>
      </defs>
      <path d="M0 24 C120 14 260 10 350 0 L350 16 C250 24 120 30 0 36 Z" fill="#f6c0ae"/>
      <path role="img" aria-label="Photo: a smiling pharmacist talking with an older couple at a pharmacy counter" d="M0 34 C120 28 250 22 350 14 L350 158 L0 158 Z" fill="url(#pharmacyGlow)"/>
      <path d="M0 158 L350 158 L350 200 L0 200 Z" fill="var(--paper)"/>
      <path d="M0 150 L120 152 C60 160 20 175 0 198 Z" fill="#c23a3a" opacity=".85"/>
      <path d="M0 200 C30 170 120 152 350 158 L350 166 C140 162 50 176 10 200 Z" fill="#f6b7a2"/>
    </svg>

    <div class="block" style="left:15px;top:450px;width:300px">
      <h2 class="heading">Transportation Services</h2>
      <div class="rule" style="margin-top:5px"></div>
      <p style="margin-top:10px">If you are a client receiving personal care services,<br>our Care Professionals can use your vehicle to drive<br>you places or run errands for you. There is no<br>additional charge for clients. Clients are responsible<br>any costs associated with transportation.</p>
      <p class="gap">Transportation services using a Brantley Care Group<br>vehicle are available to our clients receiving personal<br>care services for an additional fee. Clients can call the<br>office to schedule this service.</p>
    </div>
    <div class="rule" style="position:absolute;left:15px;top:650px"></div>
    <p class="block contact" style="left:17px;top:662px">For more information please check our website<br><em>http://www.brantleycaregroup.example/homecare/</em> ,<br>or call us at 808-555-0142.</p>
  </section>
</main>
</body>
</html>
```